Transform Your Giving

I need a tri-fold brochure that will fit in a standard number 10 business envelope. Meadowlark and Allied Services is a charitable nonprofit. The goal of this brochure is to stimulate people into thinking about other ways to make a donation. The design should communicate the essential information on donation options, create a sense of professional integrity, be graphically sharp, easy to read and laid out in a way that doesn't make the material appear crowded.

```html
<!DOCTYPE html>
<html lang="en">
<head>
<meta charset="utf-8">
<title>Transform Your Giving – Tri-fold Brochure</title>
<link rel="stylesheet" href="https://fonts.googleapis.com/css2?family=Oswald:wght@500;600&family=Montserrat:ital,wght@0,400;0,500;0,600;0,700;1,600;1,700&display=swap">
<style>
:root{
  --navy:#2d2675;
  --navy-mid:#3b3090;
  --violet:#5645b5;
  --green:#4cb848;
  --green-dark:#3fa23c;
  --ink:#2b2b33;
  --paper:#ffffff;
  --bg:#efeff0;
}
*{box-sizing:border-box;margin:0;padding:0}
html,body{width:720px;height:1200px;overflow:hidden;background:var(--bg)}
body{position:relative;font-family:"Montserrat",sans-serif;color:var(--ink)}
.sheet{position:absolute;left:32px;width:655px;height:506px;display:flex;box-shadow:0 1px 4px rgba(0,0,0,.18);background:var(--paper)}
.sheet--outside{top:68px}
.sheet--inside{top:643px}
.panel{position:relative;width:218.33px;height:100%;overflow:hidden}
.panel--navy{background:linear-gradient(90deg,var(--navy) 0%,var(--navy-mid) 55%,var(--navy) 100%);color:#fff}
.abs{position:absolute}
.body-text{font-size:6.4px;line-height:8px;font-weight:500}
.pill-head{position:absolute;background:var(--green);color:#fff;font-weight:700;font-size:7.6px;letter-spacing:.3px;padding:2px 5px;border-radius:0 6px 6px 0;line-height:9px;white-space:nowrap}
.sec-title{font-weight:700;color:var(--navy);font-size:8.2px;line-height:9.6px}
.sec-sub{font-weight:700;font-style:italic;color:var(--navy);font-size:6.3px;line-height:7.8px}
.checklist{list-style:none}
.checklist li{position:relative;padding-left:9px;font-size:6.4px;line-height:8px;font-weight:500}
.checklist li svg{position:absolute;left:0;top:1.5px;width:5px;height:5px}
.brand-word{font-family:"Montserrat",sans-serif;font-weight:700;text-align:center}
.display-title{font-family:"Oswald",sans-serif;font-weight:600}
.photo{position:absolute}
.bubble{position:absolute;width:54px;height:54px;border-radius:50%;background:radial-gradient(circle at 40% 35%,rgba(255,255,255,.92),rgba(230,230,240,.7));box-shadow:0 0 4px rgba(255,255,255,.8);display:flex;flex-direction:column;align-items:center;justify-content:center;color:var(--navy);font-weight:700;font-size:5.6px;line-height:6.4px;text-align:center}
.bubble svg{width:20px;height:18px;margin-bottom:2px}
</style>
</head>
<body>

<!-- OUTSIDE SPREAD -->
<section class="sheet sheet--outside">

  <!-- Inside flap: impact -->
  <div class="panel">
    <svg class="abs" style="left:0;top:0" width="218" height="372" viewBox="0 0 218 372" preserveAspectRatio="none">
      <defs>
        <linearGradient id="impactPhoto" x1="0" y1="0" x2="1" y2="1">
          <stop offset="0" stop-color="#8a9a4e"/><stop offset=".45" stop-color="#d9b8a8"/><stop offset="1" stop-color="#e9c7c4"/>
        </linearGradient>
      </defs>
      <rect width="218" height="345" fill="url(#impactPhoto)" role="img" aria-label="Photo of a smiling older woman in glasses reading a book outdoors"/>
      <path d="M0,306 C70,280 160,282 218,352 L218,372 L0,372Z" fill="var(--green)"/>
      <path d="M0,318 C70,296 160,300 218,372 L0,372Z" fill="#fff"/>
    </svg>
    <div class="abs" style="left:0;top:335px;height:22px;width:151px;background:var(--navy);border-radius:0 11px 11px 0"></div>
    <svg class="abs" style="left:15px;top:335px" width="128" height="22" viewBox="0 0 128 22">
      <text x="0" y="16.5" class="display-title" font-size="15" fill="#fff" font-weight="500" textLength="126" lengthAdjust="spacingAndGlyphs">THE IMPACT OF YOUR GIFT</text>
    </svg>
    <p class="abs body-text" style="left:15px;top:372px;width:192px">Your generosity drives our mission. With every Smart gift you're supporting Meadowlark and Allied Services. Join our community of Smart Givers today and make an enduring impact. With Smart Giving your generosity reaches further. Begin your Smart Giving journey with us today.</p>
    <ul class="abs checklist" style="left:15px;top:433px">
      <li style="margin-bottom:6px"><svg viewBox="0 0 10 10"><rect x=".5" y=".5" width="9" height="9" fill="none" stroke="var(--navy)"/><path d="M2,5 L4.3,7.3 L8.5,2" fill="none" stroke="var(--navy)" stroke-width="1.3"/></svg>Stocks and Securities</li>
      <li style="margin-bottom:6px"><svg viewBox="0 0 10 10"><rect x=".5" y=".5" width="9" height="9" fill="none" stroke="var(--navy)"/><path d="M2,5 L4.3,7.3 L8.5,2" fill="none" stroke="var(--navy)" stroke-width="1.3"/></svg>DAFs</li>
      <li style="margin-bottom:6px"><svg viewBox="0 0 10 10"><rect x=".5" y=".5" width="9" height="9" fill="none" stroke="var(--navy)"/><path d="M2,5 L4.3,7.3 L8.5,2" fill="none" stroke="var(--navy)" stroke-width="1.3"/></svg>QCDs</li>
      <li style="margin-bottom:6px"><svg viewBox="0 0 10 10"><rect x=".5" y=".5" width="9" height="9" fill="none" stroke="var(--navy)"/><path d="M2,5 L4.3,7.3 L8.5,2" fill="none" stroke="var(--navy)" stroke-width="1.3"/></svg>Crypto</li>
      <li><svg viewBox="0 0 10 10"><rect x=".5" y=".5" width="9" height="9" fill="none" stroke="var(--navy)"/><path d="M2,5 L4.3,7.3 L8.5,2" fill="none" stroke="var(--navy)" stroke-width="1.3"/></svg>Charitable Annuity</li>
    </ul>
  </div>

  <!-- Back panel: contact -->
  <div class="panel panel--navy">
    <p class="abs" style="left:14px;top:17px;width:190px;text-align:center;font-size:6.3px;line-height:8px;font-weight:500">To learn more about Smart Giving Options and how they can benefit you and Meadowlark and Allied Services, please reach out to our team. We're here to help you navigate these giving methods and answer any question you may have.</p>

    <div class="abs" style="left:15px;top:70px;width:189px;height:64px;background:#fff;border-radius:10px">
      <svg class="abs" style="left:0;top:0" width="189" height="64" viewBox="0 0 189 64">
        <text x="6" y="26" font-family="Oswald,sans-serif" font-size="26" font-weight="600" fill="var(--green)">“</text>
        <path d="M38,11 H180 Q184,11 184,15 V46 Q184,50 180,50 H118" fill="none" stroke="var(--green)" stroke-width=".9"/>
        <text x="88" y="64" font-family="Oswald,sans-serif" font-size="26" font-weight="600" fill="var(--green)">”</text>
      </svg>
      <p class="abs" style="left:6px;top:24px;width:165px;font-style:italic;color:var(--violet);font-size:8.4px;line-height:10px;font-weight:400">Being kind to others is a way of being good to yourself.<br><b style="font-weight:700;color:var(--navy)">- Miriam Ashford</b></p>
    </div>

    <div class="abs brand-word" style="left:10px;top:158px;width:198px;color:#fff;font-size:10px;line-height:12px">
      <span style="display:inline-block;width:7px;height:7px;border-radius:50%;background:#fff;margin-right:4px;vertical-align:0"></span>Meadowlark and Allied<br>Services, Inc.
    </div>

    <div class="abs" style="left:29px;top:210px;width:161px;height:31px;background:var(--green);border-radius:8px;text-align:center;font-size:6.3px;line-height:8px;font-weight:500;padding-top:4px">If you do not have a will, go to<br><b>www.EasyWillNow.org</b><br>In 20 minutes you can have a legal will for free.</div>

    <h3 class="abs" style="left:0;width:218px;top:270px;text-align:center;font-size:8.2px;font-weight:700;text-decoration:underline">CONTACT US</h3>
    <p class="abs" style="left:0;width:218px;top:288px;text-align:center;font-size:6.4px;line-height:8px;font-weight:500">Have more question?<br>Please contact us at Meadowlark &amp; Allied Services</p>

    <svg class="abs" style="left:104px;top:306px" width="10" height="10" viewBox="0 0 10 10"><circle cx="5" cy="5" r="5" fill="var(--green)"/><path d="M5,2.2 a1.8,1.8 0 0 1 1.8,1.8 C6.8,5.3 5,7.6 5,7.6 S3.2,5.3 3.2,4 A1.8,1.8 0 0 1 5,2.2z" fill="#fff"/></svg>
    <p class="abs" style="left:0;width:218px;top:318px;text-align:center;font-size:6.4px;line-height:8px;font-weight:500">1420 Prairie View Rd.<br>Suite 2, Fargo, ND&nbsp; 58102</p>

    <svg class="abs" style="left:104px;top:337px" width="10" height="10" viewBox="0 0 10 10"><circle cx="5" cy="5" r="5" fill="var(--green)"/><path d="M3.2,2.6 L4.3,2.4 L4.9,3.9 L4.2,4.5 Q4.9,5.6 5.6,6 L6.2,5.3 L7.6,5.9 L7.4,7 Q5.8,7.6 4.1,5.8 Q2.6,4.2 3.2,2.6z" fill="#fff"/></svg>
    <p class="abs" style="left:0;width:218px;top:350px;text-align:center;font-size:6.4px;font-weight:500">555-014-2200 (ext. 100)</p>

    <svg class="abs" style="left:104px;top:361px" width="10" height="10" viewBox="0 0 10 10"><circle cx="5" cy="5" r="5" fill="var(--green)"/><rect x="2.6" y="3.3" width="4.8" height="3.4" fill="#fff"/><path d="M2.6,3.3 L5,5.2 L7.4,3.3" fill="none" stroke="var(--green)" stroke-width=".5"/></svg>
    <p class="abs" style="left:0;width:218px;top:374px;text-align:center;font-size:6.4px;font-weight:500">giving@meadowlarkallied.org</p>

    <svg class="abs" style="left:104px;top:386px" width="10" height="10" viewBox="0 0 10 10"><circle cx="5" cy="5" r="5" fill="var(--green)"/><circle cx="5" cy="5" r="2.6" fill="none" stroke="#fff" stroke-width=".6"/><path d="M2.4,5 H7.6 M5,2.4 V7.6" stroke="#fff" stroke-width=".5"/></svg>
    <p class="abs" style="left:0;width:218px;top:398px;text-align:center;font-size:6.4px;font-weight:500">www.meadowlarkallied.org</p>

    <h3 class="abs" style="left:0;width:218px;top:428px;text-align:center;font-size:8.2px;font-weight:700;text-decoration:underline">Follow us:</h3>
    <svg class="abs" style="left:78px;top:443px" width="62" height="12" viewBox="0 0 62 12">
      <path d="M6,6 H56" stroke="var(--green)" stroke-width=".8"/>
      <circle cx="6" cy="6" r="5.5" fill="var(--green)"/>
      <circle cx="31" cy="6" r="5.5" fill="var(--green)"/>
      <circle cx="56" cy="6" r="5.5" fill="var(--green)"/>
    </svg>

    <p class="abs" style="left:20px;top:471px;width:178px;text-align:center;font-size:3.8px;line-height:4.8px">This material is provided for general information only and is not intended as tax, accounting or legal advice. Meadowlark and Allied Services is not a professional fiduciary organization. Please consult your tax advisor or financial professional before making any decision about Smart Giving.</p>
  </div>

  <!-- Front cover -->
  <div class="panel">
    <svg class="abs" style="left:12px;top:13px" width="194" height="26" viewBox="0 0 194 26">
      <text x="0" y="22" class="display-title" font-size="25" fill="var(--green)" textLength="193" lengthAdjust="spacingAndGlyphs">TRANSFORM YOUR GIVING</text>
    </svg>
    <div class="abs" style="left:23px;top:42px;width:173px;height:15px;background:var(--navy);border-radius:8px;color:#fff;text-align:center;font-weight:700;font-size:11px;line-height:15px;letter-spacing:.4px;white-space:nowrap">BE STRATEGIC, BE SMART</div>
    <p class="abs" style="left:0;width:218px;top:62px;text-align:center;font-size:8.6px;line-height:11px;font-weight:400;color:var(--ink)">Discover the impact of Smart Giving with<br>Meadowlark and Allied Services</p>

    <svg class="abs" style="left:0;top:86px" width="218" height="420" viewBox="0 0 218 420" preserveAspectRatio="none">
      <defs>
        <linearGradient id="coverPhoto" x1="0" y1="0" x2="1" y2="1">
          <stop offset="0" stop-color="#8c7f5a"/><stop offset=".4" stop-color="#9fa6b8"/><stop offset=".7" stop-color="#b86a58"/><stop offset="1" stop-color="#a07a4c"/>
        </linearGradient>
      </defs>
      <rect y="0" width="218" height="350" fill="url(#coverPhoto)" role="img" aria-label="Photo of a laughing older couple walking arm in arm through autumn woods"/>
      <path d="M0,0 H218 V0 C170,40 90,40 0,0Z" fill="#fff"/>
      <path d="M20,0 C80,40 170,45 218,0 V25 C170,55 90,50 20,0Z" fill="var(--green)"/>
      <path d="M0,0 H218 C170,30 80,33 20,0Z" fill="#fff"/>
      <path d="M0,350 C60,300 150,290 218,350 V360 H0Z" fill="var(--navy)"/>
      <path d="M0,362 C60,315 150,306 218,356 V420 H0Z" fill="#fff"/>
    </svg>

    <div class="bubble" style="left:16px;top:117px"><svg viewBox="0 0 20 18"><circle cx="6" cy="6" r="4.5" fill="none" stroke="var(--navy)" stroke-width="1.3"/><circle cx="14" cy="6" r="4.5" fill="none" stroke="var(--navy)" stroke-width="1.3"/><circle cx="10" cy="12.5" r="4.5" fill="none" stroke="var(--navy)" stroke-width="1.3"/></svg>Crypto</div>
    <div class="bubble" style="left:149px;top:148px"><svg viewBox="0 0 20 18"><path d="M6,17 L1,11.5 A3,3 0 0 1 6,7.5 A3,3 0 0 1 11,11.5Z" fill="var(--navy)"/><circle cx="14" cy="6" r="4.5" fill="none" stroke="var(--navy)" stroke-width="1.3"/></svg>DAF's</div>
    <div class="bubble" style="left:16px;top:250px"><svg viewBox="0 0 20 18"><rect x="3" y="9" width="2.5" height="8" fill="var(--navy)"/><rect x="7.5" y="6" width="2.5" height="11" fill="var(--navy)"/><rect x="12" y="8" width="2.5" height="9" fill="var(--navy)"/><rect x="16.5" y="4" width="2.5" height="13" fill="var(--navy)"/><path d="M2,6 L8,2 L13,5 L19,1" fill="none" stroke="var(--navy)" stroke-width="1.2"/></svg>Stocks &amp;<br>Securities</div>
    <div class="bubble" style="left:149px;top:282px"><svg viewBox="0 0 20 18"><rect x="3" y="5" width="14" height="4" fill="var(--navy)"/><rect x="4" y="9.5" width="12" height="8" fill="var(--navy)"/><path d="M10,5 V18" stroke="#fff" stroke-width="1.2"/><path d="M10,5 C7,0 4,2 7,5 M10,5 C13,0 16,2 13,5" fill="none" stroke="var(--navy)" stroke-width="1.3"/></svg>QCDs</div>
    <div class="bubble" style="left:16px;top:355px"><svg viewBox="0 0 20 18"><ellipse cx="6" cy="15" rx="4" ry="1.6" fill="var(--navy)"/><ellipse cx="6" cy="12" rx="4" ry="1.6" fill="var(--navy)"/><ellipse cx="13" cy="15" rx="4" ry="1.6" fill="var(--navy)"/><circle cx="15" cy="5" r="3.5" fill="var(--navy)"/></svg>Charitable<br>Annuity</div>

    <div class="abs brand-word" style="left:8px;top:456px;width:202px;color:var(--navy);font-size:10.5px;line-height:13px">
      <span style="display:inline-block;width:8px;height:8px;border-radius:50%;background:var(--green);margin-right:4px;vertical-align:0"></span>Meadowlark and Allied<br>Services, Inc.
    </div>
  </div>
</section>

<!-- INSIDE SPREAD -->
<section class="sheet sheet--inside">

  <!-- Inside left -->
  <div class="panel">
    <div class="abs" style="left:0;top:15px;width:207px;height:49px;background:var(--navy);border-radius:0 25px 25px 0;color:#fff;font-style:italic;font-weight:700;font-size:6.3px;line-height:8px;padding:4px 12px 0 15px">We would like to introduce you to five Strategic &amp; Smart ways to give that could potentially be more beneficial to you compared to traditional cash donations. We encourage you to keep this information as a guide for your future contributions.</div>

    <svg class="abs" style="left:15px;top:83px" width="38" height="32" viewBox="0 0 38 32">
      <path d="M1,2 V31 H37" fill="none" stroke="var(--green)" stroke-width="2"/>
      <rect x="6" y="18" width="4" height="11" fill="var(--green)"/><rect x="13" y="12" width="4" height="17" fill="var(--green)"/><rect x="20" y="16" width="4" height="13" fill="var(--green)"/><rect x="27" y="9" width="4" height="20" fill="var(--green)"/>
      <path d="M5,12 L13,5 L21,9 L32,2" fill="none" stroke="var(--green)" stroke-width="1.6"/>
    </svg>
    <div class="abs" style="left:60px;top:78px;width:152px">
      <h2 class="sec-title">Gifts of Stocks or Appreciated Assets Strategic &amp; Smart</h2>
      <p class="sec-sub">Consider your long-term publicly traded stock as a way to give to your favorite charity.</p>
    </div>
    <p class="abs body-text" style="left:15px;top:130px;width:194px">You can make a significantly bigger impact when you donate long-term appreciated securities, including stock, mutual funds, and bonds, directly to your favorite charity.</p>
    <div class="pill-head" style="left:14px;top:167px">HOW DOES IT WORK?</div>
    <p class="abs body-text" style="left:15px;top:191px;width:194px">When you donate stock to a charity, you will generally take a tax deduction for the full market value. Because you are donating stock, your contribution and tax deduction may be significantly higher than contributing the after-tax proceeds. The same benefits apply when you donate mutual funds or bonds.</p>

    <svg class="abs" style="left:15px;top:255px" width="36" height="34" viewBox="0 0 36 34">
      <path d="M12,33 L2,22 A6,6 0 0 1 12,15 A6,6 0 0 1 22,22Z" fill="var(--green)"/>
      <circle cx="25" cy="11" r="8.5" fill="var(--green)"/>
      <text x="25" y="15" font-family="Montserrat,sans-serif" font-weight="700" font-size="11" fill="#fff" text-anchor="middle">$</text>
      <path d="M8,10 A10,10 0 0 1 14,4 M30,24 A10,10 0 0 1 24,30" fill="none" stroke="var(--navy)" stroke-width="1"/>
    </svg>
    <div class="abs" style="left:60px;top:254px;width:152px">
      <h2 class="sec-title">Donor-Advised Fund (DAF)<br>Strategic &amp; Smart</h2>
      <p class="sec-sub">Consider a DAF – a simple, flexible, and tax-advantageous way to give to your favorite charities.</p>
    </div>
    <p class="abs body-text" style="left:15px;top:307px;width:194px">A Donor-Advised Fund (DAF), is like a charitable investment account for the sole purpose of supporting your favorite charities.</p>
    <div class="pill-head" style="left:14px;top:339px">HOW DOES IT WORK?</div>
    <p class="abs body-text" style="left:15px;top:358px;width:194px">You establish a DAF and contribute cash, stocks, or non-publicly traded assets, cryptocurrency, and private company stock to be eligible for an immediate tax deduction. Those funds are contributed for tax-free growth. You can recommend grants be made from your DAF to any IRS qualified public charity.</p>

    <svg class="abs" style="left:0;top:414px" width="218" height="92" viewBox="0 0 218 92" preserveAspectRatio="none">
      <defs><linearGradient id="grassPhoto" x1="0" y1="0" x2="1" y2="1"><stop offset="0" stop-color="#9fb08a"/><stop offset=".5" stop-color="#6f8a6a"/><stop offset="1" stop-color="#5f8a3c"/></linearGradient></defs>
      <path d="M0,8 C80,-6 160,2 218,80 V92 H0Z" fill="var(--navy)"/>
      <path d="M0,20 C80,6 150,20 204,92 H0Z" fill="url(#grassPhoto)" role="img" aria-label="Photo of a happy couple lying on the grass in a park"/>
    </svg>
  </div>

  <!-- Inside middle -->
  <div class="panel panel--navy" style="background:linear-gradient(180deg,#e8e8ee 0%,#dfe0e6 38%,#7a6fbf 52%,var(--violet) 58%,var(--navy-mid) 80%,var(--navy) 100%)">
    <div class="photo" style="left:0;top:0;width:218px;height:275px;background:linear-gradient(180deg,#ecedf1 0%,#d8d4d0 30%,#b8a49a 55%,rgba(70,60,150,.6) 85%,rgba(86,69,181,0) 100%)" role="img" aria-label="Photo of an older couple on a sofa looking at a tablet together"></div>

    <svg class="abs" style="left:15px;top:281px" width="33" height="40" viewBox="0 0 33 40">
      <rect x="1" y="11" width="31" height="8" fill="var(--green)"/>
      <rect x="3" y="21" width="27" height="19" fill="var(--green)"/>
      <path d="M16.5,11 V40" stroke="var(--navy-mid)" stroke-width="3"/>
      <path d="M16.5,10 C11,0 4,3 10,10 M16.5,10 C22,0 29,3 23,10" fill="none" stroke="var(--green)" stroke-width="2.4"/>
    </svg>
    <div class="abs" style="left:55px;top:278px;width:160px;color:#fff">
      <h2 class="sec-title" style="color:#fff">Qualified Charitable Distributions (QCDs) Strategic &amp; Smart</h2>
      <p class="sec-sub" style="color:#fff">Consider a QCD – when planning your IRA withdrawal strategy...and donate to your favorite charity.</p>
    </div>
    <p class="abs body-text" style="left:15px;top:334px;width:194px">IRA owners at age 70 or over can transfer dollars from their IRA to charity tax-free each year. These transfers known as Qualified Charitable Distributions (QCDs) offer eligible older Americans a great way to easily give to charity.</p>
    <div class="pill-head" style="left:14px;top:386px">HOW DOES IT WORK?</div>
    <p class="abs body-text" style="left:15px;top:409px;width:194px">Are you 72 and required to take a minimum distribution (RMD) from your IRA but do not need the funds? Consider a Qualified Charitable Distribution. Normally, distributions from a traditional IRA are taxable when received. With a QCD, these distributions become tax-free when paid directly from the IRA to your favorite eligible charity.&nbsp; An IRA owner wishing to make a QCD should contact their IRA trustee, allowing time to complete the transaction before the end of the year to receive the tax benefit.</p>
  </div>

  <!-- Inside right -->
  <div class="panel">
    <svg class="abs" style="left:15px;top:14px" width="33" height="30" viewBox="0 0 33 30">
      <circle cx="8" cy="9" r="7" fill="none" stroke="var(--green)" stroke-width="2"/>
      <circle cx="24" cy="9" r="7" fill="none" stroke="var(--green)" stroke-width="2"/>
      <circle cx="16" cy="21" r="7" fill="var(--green)"/>
      <text x="8" y="12" font-size="8" font-weight="700" fill="var(--navy)" text-anchor="middle" font-family="Montserrat,sans-serif">B</text>
      <text x="24" y="12" font-size="8" font-weight="700" fill="var(--navy)" text-anchor="middle" font-family="Montserrat,sans-serif">$</text>
      <path d="M16,16 L13,21 L16,26 L19,21Z" fill="#fff"/>
    </svg>
    <div class="abs" style="left:55px;top:14px;width:160px">
      <h2 class="sec-title">Cryptocurrency Strategic &amp; Smart</h2>
      <p class="sec-sub">Consider donating Bitcoin and other cryptocurrencies to your favorite charity.</p>
    </div>
    <p class="abs body-text" style="left:15px;top:55px;width:194px">Bitcoin and other cryptocurrencies can be donated to charity just like other appreciated assets such as stocks and other business interests. Before you sell bitcoin and donate the after-tax proceeds, consider donating your bitcoin directly to a favorite charity.</p>
    <div class="pill-head" style="left:14px;top:105px">HOW DOES IT WORK?</div>
    <p class="abs body-text" style="left:15px;top:127px;width:194px">Many donors find it useful to open a Donor-Advised Fund (DAF). This strategy includes two significant benefits, both for you and your favorite charity.</p>
    <ul class="abs checklist" style="left:15px;top:161px;width:194px">
      <li style="padding-left:13px;margin-bottom:3px"><svg viewBox="0 0 10 10" style="width:6px;height:6px"><rect x=".5" y=".5" width="9" height="9" fill="none" stroke="var(--navy)"/><path d="M2,5 L4.3,7.3 L8.5,2" fill="none" stroke="var(--navy)" stroke-width="1.3"/></svg>Your tax deduction will be equal to the fair market value of the donated bitcoin (as determined by a qualified appraisal).</li>
      <li style="padding-left:13px"><svg viewBox="0 0 10 10" style="width:6px;height:6px"><rect x=".5" y=".5" width="9" height="9" fill="none" stroke="var(--navy)"/><path d="M2,5 L4.3,7.3 L8.5,2" fill="none" stroke="var(--navy)" stroke-width="1.3"/></svg>Your cryptocurrency donation is tax-smart because it may eliminate capital gains taxes on the value /appreciation AND your favorite charity will receive&nbsp; 100% of the value of the contribution.</li>
    </ul>
    <p class="abs body-text" style="left:15px;top:234px;width:194px">Often charities are not able to accept direct donations of bitcoin/crypto so using a DAF is a great way to donate these assets.</p>

    <svg class="abs" style="left:15px;top:272px" width="33" height="34" viewBox="0 0 33 34">
      <path d="M1,4 H10 M1,7.5 H8 M1,11 H6" stroke="var(--green)" stroke-width="1.2"/>
      <circle cx="24" cy="6" r="4.5" fill="var(--green)"/>
      <path d="M24,11 C18,16 18,24 24,26 C30,24 30,16 24,11Z" fill="var(--green)"/>
      <ellipse cx="7" cy="31" rx="5.5" ry="2.2" fill="var(--green)"/><ellipse cx="7" cy="27" rx="5.5" ry="2.2" fill="var(--green)"/><ellipse cx="7" cy="23" rx="5.5" ry="2.2" fill="var(--green)"/>
      <ellipse cx="19" cy="31" rx="5.5" ry="2.2" fill="var(--green)"/>
    </svg>
    <div class="abs" style="left:55px;top:273px;width:160px">
      <h2 class="sec-title">Charitable Gift Annuity<br>Strategic &amp; Smart</h2>
      <p class="sec-sub">Consider establishing a Charitable<br>Gift Annuity</p>
    </div>
    <p class="abs body-text" style="left:15px;top:320px;width:194px">You make a donation to a single charity. The gift is set aside in a reserve account and invested.</p>
    <div class="pill-head" style="left:14px;top:341px">HOW DOES IT WORK?</div>
    <p class="abs body-text" style="left:15px;top:363px;width:194px">A charitable gift annuity is a contract between a donor and a charity. As a donor, you make a sizable gift to charity using cash, securities, or possibly other assets. This money is then invested.&nbsp; In return, you become eligible to take a partial tax deduction for your donation, plus you receive a fixed stream of income from the charity for the rest of your life. At the end of your life (as well as your spouse's, if you're giving as a couple), the charity receives the remainder of the gift.</p>

    <svg class="abs" style="left:0;top:440px" width="218" height="66" viewBox="0 0 218 66" preserveAspectRatio="none">
      <path d="M0,66 C40,20 140,8 218,6 V20 C140,20 60,30 6,66Z" fill="var(--green)"/>
      <path d="M6,66 C60,30 140,22 218,20 V66Z" fill="var(--navy)"/>
    </svg>
    <p class="abs" style="right:15px;top:478px;color:#fff;font-size:11px;font-weight:400;white-space:nowrap">www.meadowlarkallied.org</p>
  </div>
</section>

</body>
</html>
```